Luxury Candle Startup Needs Modern Packaging Box & Matching Label Design

We are Lumavale, a luxury candle company about to launch in Australia and we need a box packaging design that is modern, minimalist, and feminine. Our target audience are females, mostly mothers, within the age range of 25-45 who are looking for high quality, handmade luxurious products. Our company is going to have a large social media presence with new mothers as we are going to show our journey with starting a business whilst on maternity leave. We would like the arch shape incorporated into the box packaging as it is beautiful and symbolises moving into a new phase in life which really represents the brand. We would like for the packaging box to be a simple white box with a sleeve insert over the box with the design to make printing easier. Our colour inspiration are very earthy colours and would like the sleeve colour to be easily changed according to the scent. For example dusky rose coloured sleeve for rose patchouli and amber scent, light coffee coloured sleeve for coffee bean cacao scent etc. Please see uploaded files for inspiration, our logo, and the type of candle jars used.
The box dimensions are:
External Dimension: 95mmW x 95mmL x 116mmH
We look forward to seeing your amazing designs!

```html
<!DOCTYPE html>
<html lang="en">
<head>
<meta charset="utf-8">
<title>Lumavale – Rose Patchouli Packaging Set</title>
<link href="https://fonts.googleapis.com/css2?family=Cormorant+Garamond:wght@500&family=Montserrat:wght@300;500&display=swap" rel="stylesheet">
<style>
  :root {
    --canvas-bg: #f2f2f2;
    --jar-white: #ffffff;
    --sleeve-rose: #f9cdcd;
    --ink-plum: #6b4450;
    --ink-mauve: #8e6a72;
    --art-rose: rgba(232, 160, 166, 0.30);
    --art-rose-fade: rgba(232, 160, 166, 0.06);
  }
  html, body { margin: 0; padding: 0; overflow: hidden; }
  .canvas {
    position: relative;
    width: 1200px;
    height: 1200px;
    background: var(--canvas-bg);
    overflow: hidden;
    color: var(--ink-plum);
  }
  p { margin: 0; line-height: 1; text-align: center; }
  .brand-name {
    font-family: "Cormorant Garamond", serif;
    font-weight: 500;
    text-transform: uppercase;
    color: var(--ink-plum);
  }
  .tagline {
    font-family: "Montserrat", sans-serif;
    font-weight: 500;
    text-transform: uppercase;
  }
  .scent-name {
    font-family: "Montserrat", sans-serif;
    font-weight: 300;
    text-transform: uppercase;
  }
  .rose-art {
    position: absolute;
    border-radius: 28px;
    background: radial-gradient(ellipse at 45% 35%, var(--art-rose) 0%, var(--art-rose-fade) 70%, rgba(249,205,205,0) 100%);
  }

  /* Jar print face */
  .jar-face {
    position: absolute;
    left: 262px;
    top: 330px;
    width: 306px;
    height: 410px;
    background: var(--jar-white);
    border-radius: 10px 10px 40px 40px;
    box-shadow: 0 18px 40px rgba(0,0,0,0.06);
  }
  .jar-lockup { position: absolute; left: 0; top: 208px; width: 306px; }
  .jar-lockup .brand-name { font-size: 44px; letter-spacing: 2px; color: var(--ink-mauve); }
  .jar-lockup .tagline-main { margin-top: 14px; font-size: 8.5px; letter-spacing: 1.8px; color: var(--ink-mauve); }
  .jar-lockup .tagline-sub { margin-top: 6px; font-size: 6.5px; letter-spacing: 1.4px; color: var(--ink-mauve); }

  /* Sleeve front panel */
  .sleeve-front {
    position: absolute;
    left: 680px;
    top: 262px;
    width: 232px;
    height: 476px;
    background: var(--sleeve-rose);
  }
  .sleeve-front .rose-art { left: 48px; top: 210px; width: 160px; height: 240px; }
  .front-lockup { position: absolute; left: 0; top: 132px; width: 232px; }
  .front-lockup .brand-name { font-size: 36px; letter-spacing: 1px; }
  .front-lockup .tagline-main { margin-top: 10px; font-size: 7px; letter-spacing: 1.2px; }
  .front-lockup .tagline-sub { margin-top: 5px; font-size: 5.5px; letter-spacing: 1px; }
  .front-scent { position: absolute; left: 0; top: 378px; width: 232px; font-size: 14px; }

  /* Arch label */
  .arch-label {
    position: absolute;
    left: 1004px;
    top: 545px;
    width: 156px;
    height: 290px;
    background: var(--sleeve-rose);
    border-radius: 78px 78px 0 0;
    overflow: hidden;
  }
  .arch-label .rose-art { left: 14px; top: 18px; width: 136px; height: 210px; }
  .arch-lockup { position: absolute; left: 0; top: 233px; width: 156px; }
  .arch-lockup .brand-name { font-size: 22px; letter-spacing: 0.5px; }
  .arch-lockup .tagline-main { margin-top: 8px; font-size: 7px; letter-spacing: 1.4px; }
  .arch-lockup .tagline-sub { margin-top: 5px; font-size: 6px; letter-spacing: 1.2px; }

  /* Flat sleeve band */
  .sleeve {
    position: absolute;
    left: 0;
    top: 872px;
    width: 1200px;
    height: 328px;
    background: var(--sleeve-rose);
  }
  .sleeve .rose-art { left: 300px; top: 12px; width: 235px; height: 285px; }
  .sleeve-lockup { position: absolute; left: 463px; top: 72px; width: 400px; }
  .sleeve-lockup .brand-name { font-size: 54px; letter-spacing: 3px; }
  .sleeve-lockup .tagline-main { margin-top: 18px; font-size: 10.5px; letter-spacing: 2.4px; }
  .sleeve-lockup .tagline-sub { margin-top: 7px; font-size: 8px; letter-spacing: 2px; }
  .sleeve-lockup .scent-name { margin-top: 24px; font-size: 21px; letter-spacing: 0.5px; }
</style>
</head>
<body>
<main class="canvas">

  <section class="jar-face">
    <div class="jar-lockup">
      <p class="brand-name">Lumavale</p>
      <p class="tagline tagline-main">Luxury Fragrance</p>
      <p class="tagline tagline-sub">Australia</p>
    </div>
  </section>

  <section class="sleeve-front">
    <div class="rose-art" role="img" aria-label="Fine line drawing of a single rose with stem and leaf"></div>
    <div class="front-lockup">
      <p class="brand-name">Lumavale</p>
      <p class="tagline tagline-main">Luxury Fragrance</p>
      <p class="tagline tagline-sub">Australia</p>
    </div>
    <p class="scent-name front-scent">Rose Patchouli</p>
  </section>

  <aside class="arch-label">
    <div class="rose-art" role="img" aria-label="Fine line drawing of a single rose with stem and leaf"></div>
    <div class="arch-lockup">
      <p class="brand-name">Lumavale</p>
      <p class="tagline tagline-main">Luxury Fragrance</p>
      <p class="tagline tagline-sub">Australia</p>
    </div>
  </aside>

  <section class="sleeve">
    <div class="rose-art" role="img" aria-label="Fine line drawing of a single rose with stem and leaves"></div>
    <div class="sleeve-lockup">
      <p class="brand-name">Lumavale</p>
      <p class="tagline tagline-main">Luxury Fragrance</p>
      <p class="tagline tagline-sub">Australia</p>
      <p class="scent-name">Rose Patchouli</p>
    </div>
  </section>

</main>
</body>
</html>
```